Animal Horse & Bedding Company Needs a Website Coded & Designed

We need a website for a new animal bedding and feed company that is visually grabbing and vibrant. We would like to see a website that displays trust, quality and confidence. Needs to be responsive and mobile friendly for all browsers and coded for both Android & IOS. SEO is also important.

Joomla or Wordpress – must be both desktop and mobile friendly with fast page load speed. Need the ability to edit ourselves in Wordpress or Joomla.

Full details attached below with some layout and content ideas.

Coding

Coded - Design and coding required

Number of Pages Required

5+ page

Font styles to use
Sans Serif

Requirements
Must have
• Needs to be responsive and mobile friendly for all browsers and coded for both Android & IOS. SEO is also important.

Wordpress – must be both desktop and mobile friendly with fast page load speed. Need the ability to edit ourselves in Wordpress.

Logo Colours:
Dark Brown
CMYK: 50 / 70 / 80 / 70
Pantone: 4625C

Orange
CMYK: 0 / 50 / 100 / 0
Pantone: 144C
Nice to have
• Use picture of building attached and super impose logo on building.

```html
<!DOCTYPE html>
<html lang="en">
<head>
<meta charset="utf-8">
<title>Haybarn Supply – Bedding &amp; Feed</title>
<link href="https://fonts.googleapis.com/css2?family=Oswald:wght@400;500;600&family=Lato:wght@400;700&display=swap" rel="stylesheet">
<style>
:root{
  --orange:#f07f1b;
  --brown:#2f1a12;
  --brown-mid:#5a3521;
  --ink:#222;
  --text:#3b3b3b;
  --grey-band:#e5e2e0;
  --white:#fff;
}
*{margin:0;padding:0;box-sizing:border-box}
html,body{width:1200px;height:3996px;overflow:hidden}
body{font-family:'Lato',sans-serif;color:var(--text);background:var(--white);position:relative}
.abs{position:absolute}
h1,h2,h3,h4,.oswald{font-family:'Oswald',sans-serif;font-weight:500}

/* header */
.search{left:62px;top:16px;width:314px;height:49px;border:1px solid #cfcfcf;border-radius:3px;display:flex;align-items:center}
.search-btn{width:48px;height:49px;margin:-1px 0 0 -1px;background:var(--orange);border-radius:3px;display:flex;align-items:center;justify-content:center}
.search span{margin-left:18px;font-size:15px;color:#888}
.brand{left:455px;top:14px;width:290px;height:60px;display:flex;align-items:center;gap:12px}
.brand-dot{width:42px;height:42px;border-radius:50%;background:var(--orange);flex:none}
.brand-name{font-family:'Oswald',sans-serif;font-weight:500;font-size:32px;letter-spacing:1px;color:var(--brown);white-space:nowrap}
.call{left:895px;top:14px;display:flex;align-items:center;gap:14px}
.call-circle{width:48px;height:48px;border-radius:50%;background:var(--orange);display:flex;align-items:center;justify-content:center}
.call small{display:block;font-size:12px;color:var(--orange)}
.call strong{font-family:'Oswald',sans-serif;font-weight:500;font-size:27px;color:var(--ink);line-height:1}
.rule-top{left:60px;top:87px;width:1080px;height:1px;background:#bbb}
.nav{left:136px;top:98px;display:flex;gap:36px;font-size:13px;font-weight:700;color:var(--ink);letter-spacing:.3px}
.nav .active{color:var(--orange)}
.head-social{left:892px;top:98px;display:flex;gap:32px}
.head-social i{width:12px;height:12px;border-radius:50%;background:var(--ink);display:block;margin-top:2px}

/* hero */
.hero{left:0;top:135px;width:1200px;height:599px;background:linear-gradient(180deg,#5d7186 0%,#8a7f6a 35%,#7a5a34 55%,#4d4a26 75%,#3b3a22 100%)}
.hero h1{position:absolute;top:92px;width:100%;text-align:center;color:var(--white);font-size:46px;line-height:50px;font-weight:600}
.hero p{position:absolute;top:208px;left:260px;width:680px;text-align:center;color:var(--white);font-size:17px;line-height:30px}
.btn-orange{background:var(--orange);color:var(--white);font-family:'Oswald',sans-serif;font-weight:500;font-size:17px;border-radius:4px;display:flex;align-items:center;justify-content:center}
.hero .btn-orange{position:absolute;left:469px;top:297px;width:262px;height:46px}
.arrow{position:absolute;top:280px;width:36px;height:36px;border-radius:50%;background:var(--orange);display:flex;align-items:center;justify-content:center}

/* section heads */
.sec-mark{width:26px;height:26px;border-radius:50%;background:var(--orange)}
.underline{height:4px;width:120px;background:var(--orange)}

/* welcome */
.welcome h2{font-size:37px;color:var(--brown)}
.body-text{font-size:17px;line-height:30px;color:var(--text);text-align:justify}
.welcome-mark{left:730px;top:830px;width:300px;height:420px;display:flex;align-items:center;justify-content:center}
.welcome-mark .ring{width:290px;height:290px;border-radius:50%;background:radial-gradient(circle,#f5e7d7 0%,#e9cfae 60%,#c98d55 100%);display:flex;align-items:center;justify-content:center}
.welcome-mark .ring span{font-family:'Oswald',sans-serif;font-weight:500;font-size:30px;color:var(--brown)}

/* values */
.values{left:0;top:1342px;width:1200px;height:555px;background:var(--grey-band)}
.value{position:absolute;top:200px;width:320px;text-align:center}
.value-icon{width:152px;height:152px;border-radius:50%;border:3px solid var(--brown);margin:0 auto;display:flex;align-items:center;justify-content:center}
.value-icon div{width:136px;height:136px;border-radius:50%;background:var(--orange);display:flex;align-items:center;justify-content:center}
.value h3{margin-top:18px;font-size:17px;color:var(--brown)}
.value p{margin-top:12px;font-size:15px;line-height:30px;color:var(--text)}

/* bedding */
.bedding-photo{left:0;top:1897px;width:600px;height:541px;background:linear-gradient(120deg,#e7a660 0%,#b76224 40%,#5a2a12 75%,#2a140b 100%)}
.bedding{left:600px;top:1897px;width:600px;height:541px;background:var(--brown)}
.checklist{list-style:none}
.checklist li{display:flex;align-items:center;gap:18px;height:30px;font-size:17px}
.tick{width:16px;height:16px;flex:none}
.btn-outline{border:2px solid var(--orange);border-radius:6px;font-family:'Oswald',sans-serif;font-weight:500;font-size:17px;display:flex;align-items:center;justify-content:center}

/* feed */
.feed-photo{left:617px;top:2770px;width:466px;height:363px;background:linear-gradient(160deg,#6f8c4a 0%,#3f5a2b 40%,#8a4a24 65%,#3a2418 100%)}

/* newsletter */
.newsletter{left:0;top:3225px;width:1200px;height:384px;background:linear-gradient(180deg,#3a2216,#2c180f)}
.newsletter h2{position:absolute;top:90px;width:100%;text-align:center;color:var(--white);font-size:37px}
.newsletter p{position:absolute;top:153px;left:210px;width:780px;text-align:center;color:var(--white);font-weight:700;font-size:16px;line-height:26px}
.email{position:absolute;left:283px;top:222px;width:499px;height:55px;border:2px solid #d9d9d9;border-radius:3px;color:var(--white);font-size:12px;display:flex;align-items:center;padding-left:12px}
.newsletter .btn-orange{position:absolute;left:790px;top:222px;width:179px;height:55px;border-radius:3px;font-size:17px;color:var(--brown)}

/* footer */
.foot-brand{left:78px;top:3700px;width:290px;text-align:center}
.foot-brand .brand-dot{margin:0 auto 14px;width:60px;height:60px}
.foot-brand .brand-name{font-size:34px}
.foot-social{left:92px;top:3848px;display:flex;gap:16px}
.foot-social i{width:33px;height:33px;border-radius:50%;display:block}
.foot-col{top:3686px}
.foot-col h4{font-size:17px;color:var(--brown);display:inline-block;border-bottom:2px solid var(--orange);padding-bottom:2px;margin-bottom:18px}
.foot-col li{list-style:none;font-size:15px;line-height:30px;padding-left:5px;color:var(--text)}
.contact-row{display:flex;gap:22px;align-items:flex-start;font-size:15px;line-height:25px;margin-bottom:24px}
.contact-row .c-ic{width:30px;height:30px;border-radius:50%;background:var(--brown);flex:none;display:flex;align-items:center;justify-content:center}
.rule-bottom{left:63px;top:3934px;width:1035px;height:1px;background:#999}
.copy{left:0;top:3950px;width:1200px;text-align:center;font-family:'Oswald',sans-serif;font-size:14px;color:var(--ink)}
</style>
</head>
<body>

<!-- header -->
<div class="abs search"><div class="search-btn"><svg width="16" height="16" viewBox="0 0 16 16"><circle cx="6.5" cy="6.5" r="4.5" fill="none" stroke="#fff" stroke-width="2"/><line x1="10" y1="10" x2="14" y2="14" stroke="#fff" stroke-width="2.4"/></svg></div><span>Search Here</span></div>
<div class="abs brand"><div class="brand-dot"></div><div class="brand-name">HAYBARN SUPPLY</div></div>
<div class="abs call"><div class="call-circle"><svg width="20" height="20" viewBox="0 0 24 24"><path d="M6.6 10.8a15 15 0 0 0 6.6 6.6l2.2-2.2c.3-.3.7-.4 1-.2 1.1.4 2.3.6 3.6.6.6 0 1 .4 1 1V20c0 .6-.4 1-1 1A17 17 0 0 1 3 4c0-.6.4-1 1-1h3.5c.6 0 1 .4 1 1 0 1.2.2 2.4.6 3.6.1.3 0 .7-.2 1z" fill="#fff"/></svg></div><div><small>Call Us Today</small><strong>+ 123 456 7890</strong></div></div>
<div class="abs rule-top"></div>
<nav class="abs nav"><span class="active">HOME</span><span>ABOUT US</span><span>BEDDING</span><span>FEED</span><span>NEWS &amp; STORIES</span><span>CONTACT US</span></nav>
<div class="abs head-social"><i></i><i></i><i></i><i></i></div>

<!-- hero -->
<section class="abs hero" role="img" aria-label="Horses grazing in an autumn pasture in front of a red barn">
  <h1>WE ARE DEDICATED IN PROVIDING HIGH QUALITY<br>PRODUCTS AND SERVICES.</h1>
  <p>Producing, buying and marketing hay and straw for x amount of years.&nbsp; Insert blub on ownership/history of key staff/owners.</p>
  <div class="btn-orange">REQUEST QUOTE BUTTON</div>
  <div class="arrow" style="left:44px"><svg width="10" height="12" viewBox="0 0 10 12"><path d="M7 1 2 6l5 5" fill="none" stroke="#fff" stroke-width="1.6"/></svg></div>
  <div class="arrow" style="left:1120px"><svg width="10" height="12" viewBox="0 0 10 12"><path d="M3 1l5 5-5 5" fill="none" stroke="#fff" stroke-width="1.6"/></svg></div>
</section>

<!-- welcome -->
<section class="welcome">
  <div class="abs sec-mark" style="left:109px;top:786px"></div>
  <h2 class="abs" style="left:111px;top:814px">WELCOME TO HAYBARN SUPPLY</h2>
  <div class="abs underline" style="left:112px;top:880px"></div>
  <p class="abs body-text" style="left:111px;top:912px;width:500px">Looking for the best bedding and feed for your horse, livestock or household pet look no further.&nbsp; We use premium locally sourced straw and hay in all of our products and are committed in providing quality products and service.Your animal deserves the very best in health and comfort to keep them healthy, strong and happy.&nbsp; Our products are designed for horses, livestock (goats, cattle and sheep), small caged animals (rabbits, guinea pigs and more).The Haybarn Supply offers supply and delivery of fresh bedding as well as removal of waste bedding.&nbsp; Let us deliver you a container of fresh straw and haul your waste bedding away.&nbsp; A full service solution that is sustainable and responsible.</p>
  <div class="abs welcome-mark"><div class="ring"><span>HAYBARN SUPPLY</span></div></div>
</section>

<!-- values -->
<section class="abs values">
  <div class="abs sec-mark" style="left:587px;top:56px"></div>
  <h2 class="abs" style="left:0;width:1200px;text-align:center;top:92px;font-size:37px;color:var(--brown)">OUR VALUES</h2>
  <div class="abs underline" style="left:540px;top:153px"></div>
  <div class="value" style="left:92px">
    <div class="value-icon"><div><svg width="70" height="70" viewBox="0 0 70 70" fill="none" stroke="#fff" stroke-width="3"><path d="M35 8 56 16v18c0 14-9 23-21 28C23 57 14 48 14 34V16z"/><path d="M25 36l7 7 14-15"/></svg></div></div>
    <h3>QUALITY GUARANTEED</h3>
    <p>Grown for quality - 100% natural with no<br>chemicals or additives</p>
  </div>
  <div class="value" style="left:437px">
    <div class="value-icon"><div><svg width="70" height="70" viewBox="0 0 70 70" fill="none" stroke="#fff" stroke-width="3"><path d="M14 24h42l-5 36H19z"/><path d="M20 24c0-8 6-12 15-12s15 4 15 12"/></svg></div></div>
    <h3>FULL SERVICE SOLUTION</h3>
    <p>Dedicated in providing a full service solution<br>of bedding supply &amp; waste removal</p>
  </div>
  <div class="value" style="left:780px">
    <div class="value-icon"><div><svg width="70" height="70" viewBox="0 0 70 70" fill="none" stroke="#fff" stroke-width="3"><circle cx="38" cy="24" r="12"/><path d="M38 17v14M34 21h7M34 28h7"/><path d="M10 48h12l10 4h14c3 0 3 4 0 4H34M22 48l16-6c4-1 6 0 18 6"/></svg></div></div>
    <h3>CONVENIENT &amp; COST EFFECTIVE</h3>
    <p>Compressed bags , pellets or bulk<br>products saving in shipping costs</p>
  </div>
</section>

<!-- bedding -->
<div class="abs bedding-photo" role="img" aria-label="Child stroking a chestnut horse in warm evening light"></div>
<section class="abs bedding">
  <div class="abs sec-mark" style="left:62px;top:88px"></div>
  <h2 class="abs" style="left:61px;top:114px;font-size:37px;color:var(--orange)">BEDDING</h2>
  <div class="abs underline" style="left:62px;top:173px"></div>
  <ul class="abs checklist" style="left:62px;top:196px;color:var(--white)">
    <li><svg class="tick" viewBox="0 0 16 16"><circle cx="8" cy="8" r="8" fill="#f07f1b"/><path d="M4.5 8.2 7 10.6l4.5-5" fill="none" stroke="#2f1a12" stroke-width="2"/></svg>100% Natural Chopped Straw</li>
    <li><svg class="tick" viewBox="0 0 16 16"><circle cx="8" cy="8" r="8" fill="#f07f1b"/><path d="M4.5 8.2 7 10.6l4.5-5" fill="none" stroke="#2f1a12" stroke-width="2"/></svg>Low Dust</li>
    <li><svg class="tick" viewBox="0 0 16 16"><circle cx="8" cy="8" r="8" fill="#f07f1b"/><path d="M4.5 8.2 7 10.6l4.5-5" fill="none" stroke="#2f1a12" stroke-width="2"/></svg>Chemical &amp; Additive Free</li>
    <li><svg class="tick" viewBox="0 0 16 16"><circle cx="8" cy="8" r="8" fill="#f07f1b"/><path d="M4.5 8.2 7 10.6l4.5-5" fill="none" stroke="#2f1a12" stroke-width="2"/></svg>Clean &amp; Highly Absorbent</li>
    <li><svg class="tick" viewBox="0 0 16 16"><circle cx="8" cy="8" r="8" fill="#f07f1b"/><path d="M4.5 8.2 7 10.6l4.5-5" fill="none" stroke="#2f1a12" stroke-width="2"/></svg>Cheaper than Wood Shavings</li>
    <li><svg class="tick" viewBox="0 0 16 16"><circle cx="8" cy="8" r="8" fill="#f07f1b"/><path d="M4.5 8.2 7 10.6l4.5-5" fill="none" stroke="#2f1a12" stroke-width="2"/></svg>Economic – less used and less wasted</li>
    <li><svg class="tick" viewBox="0 0 16 16"><circle cx="8" cy="8" r="8" fill="#f07f1b"/><path d="M4.5 8.2 7 10.6l4.5-5" fill="none" stroke="#2f1a12" stroke-width="2"/></svg>Environmentally Friendly – Recyclable &amp; Compostable</li>
  </ul>
  <div class="abs btn-outline" style="left:60px;top:426px;width:172px;height:50px;color:var(--white)">LEARN MORE</div>
</section>

<!-- feed -->
<section class="feed">
  <div class="abs sec-mark" style="left:587px;top:2536px"></div>
  <h2 class="abs" style="left:0;width:1200px;text-align:center;top:2564px;font-size:37px;color:var(--brown)">FEED</h2>
  <div class="abs underline" style="left:565px;top:2624px;width:74px"></div>
  <p class="abs" style="left:150px;top:2656px;width:900px;text-align:center;font-size:17px;line-height:30px">Hay cubes and pellets are made from premium hay offering a variety of animals a feed that is non-GMO and packed with natural nutrients.&nbsp; These pellets and cubes are less bulky to handle, store and ship. As well, they reduce the amount of wasted feed.</p>
  <ul class="abs checklist" style="left:170px;top:2787px;color:var(--text)">
    <li><svg class="tick" viewBox="0 0 16 16"><circle cx="8" cy="8" r="8" fill="#f07f1b"/><path d="M4.5 8.2 7 10.6l4.5-5" fill="none" stroke="#fff" stroke-width="2"/></svg>100% Natural</li>
    <li><svg class="tick" viewBox="0 0 16 16"><circle cx="8" cy="8" r="8" fill="#f07f1b"/><path d="M4.5 8.2 7 10.6l4.5-5" fill="none" stroke="#fff" stroke-width="2"/></svg>Chemical &amp; Additive Free</li>
    <li><svg class="tick" viewBox="0 0 16 16"><circle cx="8" cy="8" r="8" fill="#f07f1b"/><path d="M4.5 8.2 7 10.6l4.5-5" fill="none" stroke="#fff" stroke-width="2"/></svg>Available in Pellets or Cubes</li>
    <li><svg class="tick" viewBox="0 0 16 16"><circle cx="8" cy="8" r="8" fill="#f07f1b"/><path d="M4.5 8.2 7 10.6l4.5-5" fill="none" stroke="#fff" stroke-width="2"/></svg>High Protein Content</li>
    <li><svg class="tick" viewBox="0 0 16 16"><circle cx="8" cy="8" r="8" fill="#f07f1b"/><path d="M4.5 8.2 7 10.6l4.5-5" fill="none" stroke="#fff" stroke-width="2"/></svg>Eliminate Waste In Feeding</li>
    <li><svg class="tick" viewBox="0 0 16 16"><circle cx="8" cy="8" r="8" fill="#f07f1b"/><path d="M4.5 8.2 7 10.6l4.5-5" fill="none" stroke="#fff" stroke-width="2"/></svg>Clean - Eliminates Dust From Feeding Baled Hay</li>
    <li><svg class="tick" viewBox="0 0 16 16"><circle cx="8" cy="8" r="8" fill="#f07f1b"/><path d="M4.5 8.2 7 10.6l4.5-5" fill="none" stroke="#fff" stroke-width="2"/></svg>Cost Effective</li>
    <li><svg class="tick" viewBox="0 0 16 16"><circle cx="8" cy="8" r="8" fill="#f07f1b"/><path d="M4.5 8.2 7 10.6l4.5-5" fill="none" stroke="#fff" stroke-width="2"/></svg>Convenient</li>
    <li><svg class="tick" viewBox="0 0 16 16"><circle cx="8" cy="8" r="8" fill="#f07f1b"/><path d="M4.5 8.2 7 10.6l4.5-5" fill="none" stroke="#fff" stroke-width="2"/></svg>Less wasted feed</li>
  </ul>
  <div class="abs btn-outline" style="left:169px;top:3087px;width:171px;height:50px;border-color:var(--brown);color:var(--brown)">LEARN MORE</div>
  <div class="abs feed-photo" role="img" aria-label="Three horses standing side by side in front of green trees"></div>
</section>

<!-- newsletter -->
<section class="abs newsletter" role="img" aria-label="Dark background with faint horses running">
  <h2>SUBSCRIBE TO NEWSLETTER</h2>
  <p>Lorem ipsum dolor sit amet, consectetur adipiscing elit, sed do eiusmod tempor incididunt ut labore et dolore magna aliqua.</p>
  <div class="email">Enter The Email</div>
  <div class="btn-orange">SUBSCRIBE</div>
</section>

<!-- footer -->
<div class="abs foot-brand"><div class="brand-dot"></div><div class="brand-name">HAYBARN SUPPLY</div></div>
<div class="abs foot-social"><i style="background:#3b5ba8"></i><i style="background:#d8457a"></i><i style="background:#2a9fe0"></i><i style="background:#e02a2a"></i><i style="background:#d8253a"></i></div>
<div class="abs foot-col" style="left:460px"><h4>QUICK LINKS</h4><ul><li>Home</li><li>About Us</li><li>Bedding</li><li>Feed</li><li>News &amp; Stories</li></ul></div>
<div class="abs foot-col" style="left:657px"><h4>IMPORTANT</h4><ul><li>Contact Us</li><li>FAQ</li><li>Privacy policy</li><li>Term &amp; condition</li></ul></div>
<div class="abs foot-col" style="left:870px;width:280px"><h4>CONTACT INFO</h4>
  <div class="contact-row" style="margin-top:2px"><div class="c-ic"><svg width="12" height="14" viewBox="0 0 12 14"><path d="M6 0a5 5 0 0 0-5 5c0 4 5 9 5 9s5-5 5-9a5 5 0 0 0-5-5z" fill="#f07f1b"/></svg></div><span>123 Lorem ipsum dolor sit amet consectetur adipiscing elit,</span></div>
  <div class="contact-row"><div class="c-ic"><svg width="13" height="13" viewBox="0 0 24 24"><path d="M6.6 10.8a15 15 0 0 0 6.6 6.6l2.2-2.2c.3-.3.7-.4 1-.2 1.1.4 2.3.6 3.6.6.6 0 1 .4 1 1V20c0 .6-.4 1-1 1A17 17 0 0 1 3 4c0-.6.4-1 1-1h3.5c.6 0 1 .4 1 1 0 1.2.2 2.4.6 3.6.1.3 0 .7-.2 1z" fill="#f07f1b"/></svg></div><span>123 456 7890</span></div>
  <div class="contact-row"><div class="c-ic"><svg width="14" height="11" viewBox="0 0 14 11"><rect x="0.5" y="0.5" width="13" height="10" fill="#f07f1b"/><path d="M1 1l6 5 6-5" fill="none" stroke="#2f1a12" stroke-width="1.2"/></svg></div><span>info@haybarnsupply.com</span></div>
</div>
<div class="abs rule-bottom"></div>
<div class="abs copy">© Copyrights 2021 Haybarn Supply &nbsp;|&nbsp;&nbsp; All Rights Reserved</div>

</body>
</html>
```